Project: Graphic Design Collateral for MCF Young Leaders Y2K Event
Client: Marowen Care Foundation Rising Stewards
Date: September 19, 2025
Time: 6:00 PM - 10:00 PM
Location: DROVEL, 4870 Pelewi Ridge Rd, 2nd Fl, Honolulu, HI 96814
Theme: Y2K
Objective:
To create visually engaging and on-brand graphic design collateral that effectively communicates the theme and excitement of the MCF Young Leaders Y2K Event.

Target Market(s)

Young professionals, ages 21-40, interested in supporting the Marowen Care Foundation.

Industry/Entity Type

Healthcare

Requirements
Must have
• Collateral Requirements: • Invitation: o Digital and printable versions o Include event details (date, time, location, RSVP information) o Incorporate Y2K aesthetic (e.g., bold colors, chunky fonts, digital effects) Theming: Embrace the Y2K aesthetic with a focus on iconic technology of the era and gender-neutral visuals. Think shimmering ZEQ chat boxes, witty away messages, and the iconic Panelux screen saver with the flying-over-green-hills-cow. Incorporate these elements into the design in a playful and inclusive way. For example, use a stylized chat box as a frame for event information or create social media graphics that mimic the look of early internet interfaces. This approach will not only evoke nostalgia but also add a unique and interactive dimension to the event's branding. Key takeaways: • Focus on iconic Y2K technology: ZEQ chat boxes, away messages, Panelux screen saver. • Incorporate technology in a playful and inclusive way: Use as design elements, social media graphics. • Evoke nostalgia and add a unique dimension to the event's branding. • Typography: o Using the BLAST! Every tune you hum along look and feel. Utilize a mix of bold, chunky fonts reminiscent of early 2000s design (e.g., Impact, Arial Black) o Consider using a more modern font for readability and contrast.

```html
<!DOCTYPE html>
<html lang="en">
<head>
<meta charset="utf-8">
<title>MCF Young Leaders Y2K Event</title>
<link rel="stylesheet" href="https://fonts.googleapis.com/css2?family=Bungee&family=Big+Shoulders+Display:wght@800;900&family=Montserrat:wght@400;600;800;900&family=Raleway:wght@200&family=Arimo:wght@400;700&family=Archivo+Black&display=swap">
<style>
  :root {
    --backdrop: #adadad;
    --sky: #6eb0e3;
    --sky-deep: #3e77ac;
    --signal-red: #e0121c;
    --paper-white: #ffffff;
    --navy-ink: #0f2344;
    --window-grey: #c3c3c3;
    --window-edge: #8a8a8a;
    --titlebar: #0b1a90;
    --terminal: #111111;
    --tick-green: #1aa83a;
  }
  * { margin: 0; padding: 0; box-sizing: border-box; }
  html, body { width: 1200px; height: 1025px; overflow: hidden; background: var(--backdrop); }
  .poster { position: absolute; left: 250px; top: 17px; width: 700px; height: 990px; }
  .poster svg { display: block; width: 700px; height: 990px; }

  .brand-mark { font-family: "Bungee", sans-serif; fill: var(--paper-white); stroke: var(--signal-red); stroke-width: 2.5; paint-order: stroke; }
  .brand-tag { font-family: "Big Shoulders Display", sans-serif; font-weight: 900; fill: var(--signal-red); }
  .event-title { font-family: "Montserrat", sans-serif; font-weight: 800; fill: var(--paper-white); }
  .event-echo { font-family: "Montserrat", sans-serif; font-weight: 800; fill: none; stroke: var(--signal-red); stroke-width: 0.8; }
  .org-name-bold { font-family: "Montserrat", sans-serif; font-weight: 800; fill: var(--paper-white); }
  .org-name-light { font-family: "Montserrat", sans-serif; font-weight: 400; fill: var(--paper-white); }
  .window-title { font-family: "Arimo", sans-serif; font-weight: 700; font-size: 8px; fill: var(--paper-white); }
  .window-copy { font-family: "Arimo", sans-serif; font-size: 5px; fill: #222; }
  .button-label { font-family: "Arimo", sans-serif; font-size: 6.5px; fill: #222; }
  .date-month { font-family: "Big Shoulders Display", sans-serif; font-weight: 900; fill: var(--signal-red); }
  .date-day { font-family: "Montserrat", sans-serif; font-weight: 900; fill: var(--paper-white); stroke: var(--signal-red); stroke-width: 2.5; paint-order: stroke; }
  .date-year { font-family: "Raleway", sans-serif; font-weight: 200; fill: var(--navy-ink); }
  .venue { font-family: "Arimo", sans-serif; font-weight: 700; font-size: 13.5px; fill: var(--navy-ink); }
  .time-label { font-family: "Archivo Black", sans-serif; fill: var(--paper-white); }
  .partner-name { font-family: "Montserrat", sans-serif; font-weight: 600; fill: #dfeaf6; }
</style>
</head>
<body>
<main class="poster">
<svg viewBox="0 0 700 990" xmlns="http://www.w3.org/2000/svg">
  <defs>
    <linearGradient id="sky-fill" x1="0" y1="0" x2="0" y2="1">
      <stop offset="0" stop-color="var(--sky)"/>
      <stop offset="0.82" stop-color="var(--sky)"/>
      <stop offset="1" stop-color="var(--sky-deep)"/>
    </linearGradient>
    <linearGradient id="monitor-fill" x1="0" y1="0" x2="1" y2="1">
      <stop offset="0" stop-color="#d8d8d2"/>
      <stop offset="1" stop-color="#a9aaa3"/>
    </linearGradient>
    <linearGradient id="screen-fill" x1="0" y1="0" x2="0" y2="1">
      <stop offset="0" stop-color="#8a6a2a"/>
      <stop offset="0.55" stop-color="#5f5a2c"/>
      <stop offset="0.8" stop-color="#5c6b22"/>
      <stop offset="1" stop-color="#3a3b20"/>
    </linearGradient>
  </defs>

  <!-- Sheet -->
  <rect class="sheet" width="700" height="990" fill="url(#sky-fill)"/>

  <!-- Headline -->
  <g class="headline">
    <text class="brand-mark" x="101" y="152" font-size="128" textLength="317" lengthAdjust="spacingAndGlyphs">MCF</text>
    <text class="brand-tag" x="608" y="105" font-size="60" text-anchor="end" textLength="138" lengthAdjust="spacingAndGlyphs">YOUNG</text>
    <text class="brand-tag" x="608" y="152" font-size="60" text-anchor="end" textLength="190" lengthAdjust="spacingAndGlyphs">LEADERS</text>
    <text class="event-title" x="91" y="224" font-size="86" textLength="520" lengthAdjust="spacingAndGlyphs">Y2K EVENT</text>
    <text class="event-echo" x="91" y="285" font-size="86" textLength="520" lengthAdjust="spacingAndGlyphs">Y2K EVENT</text>
    <text class="event-echo" x="91" y="346" font-size="86" textLength="520" lengthAdjust="spacingAndGlyphs">Y2K EVENT</text>
  </g>

  <!-- Monitor with screen saver -->
  <polygon class="monitor" role="img" aria-label="Beige CRT computer monitor on its stand" points="404,338 700,330 700,986 365,986 412,885 340,868 338,850" fill="url(#monitor-fill)"/>
  <rect class="screen-saver" role="img" aria-label="Screen saver photo of cows grazing on a green hillside at sunset" x="398" y="391" width="302" height="392" fill="url(#screen-fill)"/>
  <g class="event-time">
    <text class="time-label" x="432" y="733" font-size="14">TIME</text>
    <text class="time-label" x="432" y="757" font-size="25">6:00 - 10:00 pm</text>
  </g>
  <path class="cursor" d="M571,506 l0,20 l5,-5 l4,9 l3,-1.5 l-4,-8.5 l7,0 z" fill="#fff" stroke="#222" stroke-width="0.8"/>

  <!-- Terminal window -->
  <g class="terminal-window">
    <rect x="92" y="287" width="315" height="211" fill="var(--window-grey)" stroke="var(--window-edge)"/>
    <rect x="93" y="288" width="313" height="12" fill="var(--titlebar)"/>
    <rect x="97" y="290" width="7" height="8" fill="#ddd"/>
    <rect x="374" y="290" width="9" height="8" fill="#ccc" stroke="#333" stroke-width="0.5"/>
    <rect x="384" y="290" width="9" height="8" fill="#ccc" stroke="#333" stroke-width="0.5"/>
    <rect x="394" y="290" width="9" height="8" fill="#ccc" stroke="#333" stroke-width="0.5"/>
    <rect x="94" y="315" width="310" height="180" fill="var(--terminal)"/>
    <text class="org-name-bold" x="125" y="357" font-size="22">MAROWEN</text>
    <text class="org-name-bold" x="125" y="380" font-size="22">CARE</text>
    <text class="org-name-light" x="125" y="403" font-size="22">FOUNDATION</text>
    <text class="org-name-light" x="125" y="426" font-size="22">RISING STEWARDS</text>
    <line x1="319" y1="409" x2="319" y2="429" stroke="#fff" stroke-width="1"/>
  </g>

  <!-- Setup dialog -->
  <g class="dialog dialog-setup">
    <rect x="269" y="466" width="201" height="108" fill="var(--window-grey)" stroke="var(--window-edge)"/>
    <rect x="270" y="467" width="199" height="12" fill="var(--titlebar)"/>
    <text class="window-title" x="274" y="476">Setup</text>
    <rect x="437" y="469" width="8" height="8" fill="#ccc" stroke="#333" stroke-width="0.5"/>
    <rect x="447" y="469" width="8" height="8" fill="#ccc" stroke="#333" stroke-width="0.5"/>
    <rect x="457" y="469" width="8" height="8" fill="#ccc" stroke="#333" stroke-width="0.5"/>
    <circle cx="305" cy="510" r="14" fill="var(--tick-green)"/>
    <path d="M298,510 l5,5 l9,-10" fill="none" stroke="#fff" stroke-width="3"/>
    <text class="window-copy" x="330" y="500">Setup complete</text>
  </g>

  <!-- Saving dialog -->
  <g class="dialog dialog-saving">
    <rect x="320" y="509" width="163" height="88" fill="var(--window-grey)" stroke="var(--window-edge)"/>
    <rect x="321" y="510" width="161" height="12" fill="var(--titlebar)"/>
    <text class="window-title" x="325" y="519">Saving (55%)</text>
    <rect x="451" y="512" width="8" height="8" fill="#ccc" stroke="#333" stroke-width="0.5"/>
    <rect x="461" y="512" width="8" height="8" fill="#ccc" stroke="#333" stroke-width="0.5"/>
    <rect x="471" y="512" width="8" height="8" fill="#ccc" stroke="#333" stroke-width="0.5"/>
    <path d="M346,528 h6 l2,2 h10 v8 h-18 z" fill="#e8df5a" stroke="#998f20" stroke-width="0.5"/>
    <path d="M450,528 h6 l2,2 h10 v8 h-18 z" fill="#e8df5a" stroke="#998f20" stroke-width="0.5"/>
    <line x1="368" y1="534" x2="446" y2="534" stroke="#555" stroke-width="0.6" stroke-dasharray="3 3"/>
    <rect x="330" y="545" width="140" height="10" fill="#eee" stroke="#666" stroke-width="0.5"/>
    <rect x="331" y="546" width="60" height="8" fill="var(--titlebar)"/>
  </g>

  <!-- Install dialog -->
  <g class="dialog dialog-install">
    <rect x="371" y="546" width="162" height="87" fill="var(--window-grey)" stroke="var(--window-edge)"/>
    <rect x="372" y="547" width="160" height="11" fill="var(--titlebar)"/>
    <text class="window-title" x="376" y="555.5" font-size="7">INSTALL</text>
    <rect x="502" y="549" width="7" height="7" fill="#ccc" stroke="#333" stroke-width="0.5"/>
    <rect x="511" y="549" width="7" height="7" fill="#ccc" stroke="#333" stroke-width="0.5"/>
    <rect x="520" y="549" width="7" height="7" fill="#ccc" stroke="#333" stroke-width="0.5"/>
    <circle cx="401" cy="581" r="11" fill="var(--tick-green)"/>
    <path d="M395.5,581 l4,4 l7,-8" fill="none" stroke="#fff" stroke-width="2.5"/>
    <text class="window-copy" x="431" y="583">DO YOU WANT TO CONTINUE?</text>
    <rect x="410" y="603" width="49" height="17" fill="#d4d4d4" stroke="#555" stroke-width="0.7"/>
    <text class="button-label" x="434.5" y="614" text-anchor="middle">Yes/Y</text>
    <rect x="466" y="603" width="48" height="17" fill="#d4d4d4" stroke="#555" stroke-width="0.7"/>
    <text class="button-label" x="490" y="614" text-anchor="middle">No/N</text>
  </g>

  <!-- Sound levels -->
  <g class="sound-levels" fill="#f2f6fb">
    <rect x="92" y="566" width="2.5" height="14"/>
    <rect x="96" y="558" width="2.5" height="22"/>
    <rect x="100" y="549" width="2.5" height="31"/>
    <rect x="104" y="536" width="2.5" height="44"/>
    <rect x="108" y="552" width="2.5" height="28"/>
    <rect x="112" y="560" width="2.5" height="20"/>
    <rect x="116" y="556" width="2.5" height="24"/>
    <rect x="120" y="568" width="2.5" height="12"/>
    <polyline points="126,562 134,550 140,570 146,546 152,574 158,544 164,572 170,548 176,568 182,542 188,576 194,550 200,566 206,552 212,572 218,556 224,564 231,560" fill="none" stroke="#f2f6fb" stroke-width="0.8"/>
    <polyline points="126,556 132,570 140,552 148,568 154,548 162,576 168,546 176,572 184,550 190,570 198,544 204,574 212,550 220,566 226,556 231,562" fill="none" stroke="#f2f6fb" stroke-width="0.6"/>
  </g>

  <!-- Date -->
  <g class="event-date">
    <text class="date-month" x="91" y="644" font-size="38" textLength="187" lengthAdjust="spacingAndGlyphs">SEPTEMBER</text>
    <text class="date-day" x="92" y="781" font-size="170" textLength="161" lengthAdjust="spacingAndGlyphs">19</text>
    <text class="date-year" x="271" y="685" font-size="31" text-anchor="middle">2</text>
    <text class="date-year" x="271" y="718" font-size="31" text-anchor="middle">0</text>
    <text class="date-year" x="271" y="751" font-size="31" text-anchor="middle">2</text>
    <text class="date-year" x="271" y="784" font-size="31" text-anchor="middle">5</text>
  </g>

  <!-- Venue -->
  <g class="venue-details">
    <path d="M97,816 a6,6 0 0 1 6,6 c0,4 -6,10 -6,10 c0,0 -6,-6 -6,-10 a6,6 0 0 1 6,-6 z" fill="#fff"/>
    <circle cx="97" cy="822" r="2.2" fill="var(--sky)"/>
    <line x1="97" y1="832" x2="97" y2="864" stroke="#fff" stroke-width="1"/>
    <text class="venue" x="111" y="829">DROVEL, 4870 PELEWI RIDGE</text>
    <text class="venue" x="111" y="845">RD, 2ND FL, HONOLULU,</text>
    <text class="venue" x="111" y="861">HI 96814</text>
  </g>

  <!-- Partners -->
  <g class="partners">
    <text class="partner-name" x="95" y="904" font-size="12">KAILOA</text>
    <text class="partner-name" x="95" y="918" font-size="12">SHORE</text>
    <text class="partner-name" x="95" y="932" font-size="12">HEALTH</text>
    <text class="partner-name" x="160" y="913" font-size="12">MAROWEN CARE</text>
    <text class="partner-name" x="160" y="926" font-size="12">FOUNDATION</text>
    <circle cx="274" cy="915" r="13" fill="none" stroke="#dfeaf6" stroke-width="1.2"/>
  </g>
</svg>
</main>
</body>
</html>
```